The Plate Compass

Cutting Through the Noise to What Actually Works.

Nutrition book

Target Market(s)

People looking to be or get healthy and eat right.

```html
<!DOCTYPE html>
<html lang="en">
<head>
<meta charset="utf-8">
<title>The Plate Compass</title>
<link rel="stylesheet" href="https://fonts.googleapis.com/css2?family=Archivo+Black&family=Fira+Sans:wght@500;600&display=swap">
<style>
  :root {
    --paper: #f7f4e8;
    --ink: #0f3320;
    --leaf: #4f8f2e;
    --rule: #2f8a5a;
    --calories: #f2b83a;
    --protein: #e8692f;
    --quality: #5b9a36;
    --timing: #2f86a8;
    --supplements: #6a4c92;
    --noise: #4a4a4a;
    --label: #ffffff;
  }
  * { margin: 0; padding: 0; box-sizing: border-box; }
  html, body { width: 800px; height: 1200px; overflow: hidden; background: var(--paper); }
  .cover { position: relative; width: 800px; height: 1200px; background: var(--paper); }
  .kicker {
    position: absolute; top: 54px; left: 0; width: 800px;
    display: flex; align-items: center; justify-content: center; gap: 34px;
  }
  .kicker-rule { width: 204px; height: 3px; background: var(--rule); }
  .kicker-text {
    font-family: "Archivo Black", sans-serif; font-size: 46px; line-height: 1;
    letter-spacing: 12px; color: var(--ink); padding-left: 12px;
  }
  .title {
    position: absolute; left: 0; width: 800px; text-align: center;
    font-family: "Archivo Black", sans-serif; font-size: 134px; line-height: 1;
    letter-spacing: -2px;
  }
  .title-top { top: 106px; color: var(--ink); }
  .title-bottom { top: 226px; color: var(--leaf); }
  .subtitle {
    position: absolute; top: 367px; left: 0; width: 800px; text-align: center;
    font-family: "Fira Sans", sans-serif; font-weight: 500; font-size: 35px;
    line-height: 48px; color: var(--ink);
  }
  .pyramid { position: absolute; top: 0; left: 0; }
  .tier-label {
    font-family: "Fira Sans", sans-serif; font-weight: 600; font-size: 19px;
    letter-spacing: 2px; fill: var(--label); text-anchor: middle;
  }
</style>
</head>
<body>
<main class="cover">
  <div class="kicker">
    <span class="kicker-rule"></span>
    <span class="kicker-text">THE</span>
    <span class="kicker-rule"></span>
  </div>
  <h1 class="title title-top">PLATE</h1>
  <h1 class="title title-bottom">COMPASS</h1>
  <p class="subtitle">Cutting Through the Noise to<br>What Actually Works.</p>

  <svg class="pyramid" width="800" height="1200" viewBox="0 0 800 1200">
    <g stroke-linejoin="round" stroke-width="10">
      <polygon points="400,480 476,594 324,594" fill="var(--calories)" stroke="var(--calories)"/>
      <polygon points="312,607 488,607 530,699 270,699" fill="var(--protein)" stroke="var(--protein)"/>
      <polygon points="257,713 540,713 580,805 219,805" fill="var(--quality)" stroke="var(--quality)"/>
      <polygon points="194,819 591,819 631,912 168,912" fill="var(--timing)" stroke="var(--timing)"/>
      <polygon points="140,927 645,927 682,1019 117,1019" fill="var(--supplements)" stroke="var(--supplements)"/>
      <polygon points="85,1034 696,1034 732,1129 68,1129" fill="var(--noise)" stroke="var(--noise)"/>
    </g>

    <path class="icon-flame" d="M400 506 C410 520 420 528 420 542 C420 555 411 563 400 563 C389 563 380 555 380 543 C380 533 386 526 390 520 C391 528 394 532 398 533 C396 522 398 514 400 506 Z" fill="#ffffff" opacity="0.92"/>
    <text class="tier-label" x="400" y="582">CALORIES</text>

    <rect x="314" y="610" width="166" height="60" rx="26" fill="#d9a25c" role="img" aria-label="Grilled chicken breast with boiled eggs"/>
    <text class="tier-label" x="400" y="692">PROTEIN</text>

    <rect x="275" y="716" width="246" height="58" rx="26" fill="#6f8f3a" role="img" aria-label="Leafy greens, berries, tomato, avocado and nuts"/>
    <text class="tier-label" x="400" y="798">FOOD QUALITY</text>

    <g class="icon-clock" fill="none" stroke="#ffffff" stroke-width="3.5" stroke-linecap="round">
      <circle cx="400" cy="853" r="26"/>
      <path d="M400 836 V855 L412 862"/>
    </g>
    <text class="tier-label" x="400" y="905">MEAL TIMING</text>

    <rect x="326" y="936" width="140" height="50" rx="24" fill="#d8cfc0" role="img" aria-label="White capsules and fish oil softgels"/>
    <text class="tier-label" x="400" y="1011">SUPPLEMENTS</text>

    <g class="icon-noise" fill="none" stroke="#ffffff" stroke-width="3.5" stroke-linecap="round">
      <circle cx="400" cy="1070" r="20"/>
      <path d="M386 1056 L414 1084"/>
      <path d="M368 1058 C362 1066 362 1074 368 1082"/>
      <path d="M360 1052 C351 1064 351 1076 360 1088"/>
      <path d="M432 1058 C438 1066 438 1074 432 1082"/>
      <path d="M440 1052 C449 1064 449 1076 440 1088"/>
    </g>
    <text class="tier-label" x="400" y="1120">NOISE</text>
  </svg>
</main>
</body>
</html>
```